Business card por a urban DJ, up scale audience target

Need a sober design, modern, conservative colors but i can consider some options, y play rnb, hip hop, EDM and top40.

Business card for contact and personal info, double sided, use logo attrached please; im 42 so i need a card acording to my age an target audience.

Target Market(s)

Adult people, up scale audience

Industry/Entity Type

Music Download

Contact Information for Business Card

Cel (318) 4207265518 www.lumadrift.com

Requirements
Must have
• open mind
Nice to have
• open mind
Should not have
• DJ

```html
<!DOCTYPE html>
<html lang="en">
<head>
<meta charset="utf-8">
<title>LUMA Business Card</title>
<link href="https://fonts.googleapis.com/css2?family=Arimo:wght@400;700&display=swap" rel="stylesheet">
<style>
  :root {
    --backdrop: #3a332f;
    --card: #161616;
    --card-edge: #0c0c0c;
    --ink: #ffffff;
    --ink-soft: #d9d9d9;
    --rule: #bdbdbd;
  }
  * { box-sizing: border-box; margin: 0; padding: 0; }
  html, body {
    width: 1200px; height: 780px; overflow: hidden;
    background: var(--backdrop);
    font-family: "Arimo", Arial, sans-serif;
  }
  .canvas {
    width: 1200px; height: 780px;
    display: flex; align-items: center; justify-content: center; gap: 40px;
  }
  .card {
    position: relative;
    width: 540px; height: 309px;
    background: var(--card);
    border: 1px solid var(--card-edge);
    border-radius: 6px;
    box-shadow: 0 10px 30px rgba(0,0,0,0.45);
    overflow: hidden;
    color: var(--ink);
  }
  .wordmark {
    display: flex; align-items: center; gap: 10px;
    font-weight: 700; color: var(--ink);
    letter-spacing: 0.02em; line-height: 1;
  }
  .wordmark-square { background: var(--ink); flex: none; }

  /* Front */
  .card-front .wordmark { position: absolute; left: 34px; top: 28px; font-size: 54px; }
  .card-front .wordmark-square { width: 12px; height: 12px; }
  .rule { position: absolute; height: 1px; background: var(--rule); }
  .rule-top { left: 0; top: 100px; width: 310px; }
  .rule-bottom { left: 310px; top: 178px; right: 0; }
  .identity { position: absolute; left: 318px; top: 112px; }
  .identity-name { font-weight: 700; font-size: 20px; }
  .identity-title { font-weight: 400; font-size: 15px; color: var(--ink-soft); margin-top: 4px; }
  .contact-list {
    position: absolute; left: 34px; top: 122px;
    list-style: none; font-size: 13px; color: var(--ink-soft);
  }
  .contact-item { display: flex; align-items: center; gap: 10px; height: 24px; }
  .contact-icon { width: 12px; height: 12px; flex: none; }

  /* Back */
  .card-back { display: flex; align-items: center; justify-content: center; }
  .card-back .wordmark { font-size: 96px; gap: 16px; }
  .card-back .wordmark-square { width: 20px; height: 20px; }
</style>
</head>
<body>
<main class="canvas">
  <section class="card card-front">
    <div class="wordmark"><span class="wordmark-square"></span>LUMA</div>
    <div class="rule rule-top"></div>
    <div class="identity">
      <p class="identity-name">Marcus Whitfield</p>
      <p class="identity-title">Managing Director</p>
    </div>
    <div class="rule rule-bottom"></div>
    <ul class="contact-list">
      <li class="contact-item">
        <svg class="contact-icon" viewBox="0 0 12 12"><rect width="12" height="12" rx="2" fill="#fff"/><path d="M3.5 2.8l1.4 0 .6 1.7-.9.7c.5 1 1.2 1.7 2.2 2.2l.7-.9 1.7.6v1.4c-3.6 0-5.7-2.1-5.7-5.7z" fill="#161616"/></svg>
        <span>(318) 4207265518</span>
      </li>
      <li class="contact-item">
        <svg class="contact-icon" viewBox="0 0 12 12"><rect width="12" height="12" rx="2" fill="#fff"/><circle cx="6" cy="6" r="3.3" fill="none" stroke="#161616" stroke-width="0.9"/><path d="M2.7 6h6.6M6 2.7c-1.6 1.8-1.6 4.8 0 6.6M6 2.7c1.6 1.8 1.6 4.8 0 6.6" fill="none" stroke="#161616" stroke-width="0.7"/></svg>
        <span>www.lumadrift.com</span>
      </li>
      <li class="contact-item">
        <svg class="contact-icon" viewBox="0 0 12 12"><rect width="12" height="12" rx="2" fill="#fff"/><rect x="2.5" y="3.5" width="7" height="5" fill="none" stroke="#161616" stroke-width="0.9"/><path d="M2.5 3.5L6 6.3 9.5 3.5" fill="none" stroke="#161616" stroke-width="0.9"/></svg>
        <span>info@lumadrift.com</span>
      </li>
      <li class="contact-item">
        <svg class="contact-icon" viewBox="0 0 12 12"><rect width="12" height="12" rx="2" fill="#fff"/><path d="M6 2.3a2.4 2.4 0 0 1 2.4 2.4C8.4 6.6 6 9.7 6 9.7S3.6 6.6 3.6 4.7A2.4 2.4 0 0 1 6 2.3z" fill="#161616"/><circle cx="6" cy="4.7" r="0.9" fill="#fff"/></svg>
        <span>214 Harbor St, Suite Easton MA 0372</span>
      </li>
    </ul>
  </section>

  <section class="card card-back">
    <div class="wordmark"><span class="wordmark-square"></span>LUMA</div>
  </section>
</main>
</body>
</html>
```